KELBRIDGE PAINTING

We are a painting company. We paint residential, commercial and strata jobs. I need the website to be very sharp, neat and elegant. I've attached our logo. the Logo needs to be embossed as a gold color and the background like a Matt black. I need these tabs:

• HOME • ABOUT US • SERVICES • TESTIMONIALS • SHOWCASE • CONTACT US

Be creative and innovative in your style.
take this as an example to just get the gist of what I'm expecting. If you can better it then the job is yours!

http://rickhalvorpainting.com.au/contact.html

I look forward to seeing your artwork :)

#These are the links to my logo in PSD format.

https://www.filevaultzy.com/s/qwertplk83nd7ha/Kelbridge%20Painting%20Luxury%20Gold.rar

https://www.filevaultzy.com/sh/bzuyrak2m5wqp9/QoPL7-xvMn

Painting

• Making the Logo embossed like the artworks i have attached is definitely a necessity.

Can you let me know if this is possible to apply to the website.

thank you

```html
<!DOCTYPE html>
<html lang="en">
<head>
<meta charset="utf-8">
<title>Kelbridge Painting</title>
<link href="https://fonts.googleapis.com/css2?family=Source+Sans+3:ital,wght@0,400;0,600;0,700;1,400&display=swap" rel="stylesheet">
<style>
:root{
  --ink:#1e232c;
  --gold:#e5b54a;
  --gold-deep:#d4a20f;
  --gold-pale:#f2d49a;
  --steel:#4f545b;
  --steel-light:#9a9da2;
  --footer:#9c9fa4;
  --white:#ffffff;
  --text-dark:#2a2d33;
}
*{margin:0;padding:0;box-sizing:border-box}
html,body{width:1054px;height:1200px;overflow:hidden;background:var(--ink)}
body{font-family:"Source Sans 3",sans-serif;color:var(--white);position:relative}
.page{position:relative;width:1054px;height:1200px}
.abs{position:absolute}

/* header */
.header{left:0;top:0;width:1054px;height:82px;background:var(--ink);border-bottom:1px solid var(--gold)}
.header-phone{right:146px;top:15px;font-size:19px;font-weight:700;color:var(--gold);display:flex;align-items:center;gap:8px}
.main-nav{right:146px;top:56px;display:flex;gap:26px;font-size:12px;font-weight:600;letter-spacing:.6px}
.main-nav a{color:var(--white);text-decoration:none}
.main-nav a.active{color:var(--gold)}

/* hero */
.hero{left:0;top:82px;width:1054px;height:396px;background:linear-gradient(100deg,#6e4f3c 0%,#8a6a55 30%,#b89a85 55%,#d9c6b6 70%,#8c6c57 100%)}
.brand-ribbon{left:243px;top:82px;width:446px;height:34px;background:linear-gradient(90deg,#e8c25e,#f6e08a 50%,#e2b849);display:flex;align-items:center;padding-left:15px}
.brand-name{font-size:20px;font-weight:700;letter-spacing:1.2px;color:var(--ink)}
.brand-divider{width:1px;height:18px;background:#b8881e;margin:0 13px}
.brand-tagline{font-size:15px;font-style:italic;color:var(--ink)}
.brand-mark{left:147px;top:22px;width:100px;height:100px;border-radius:50%;background:var(--ink)}
.slider-dots{left:852px;top:109px;display:flex;gap:7px}
.slider-dots span{width:8px;height:8px;background:#3a3d42}
.slider-dots span.on{background:var(--gold)}

.hero-caption{left:154px;top:303px;width:560px;height:122px;background:var(--ink);padding:16px 0 0 32px;font-size:38px;line-height:44px;font-weight:400}
.accent-left{left:145px;top:295px;width:9px;height:48px;background:var(--gold)}
.accent-top-left{left:145px;top:295px;width:48px;height:8px;background:var(--gold)}
.accent-corner-right{left:714px;top:345px;width:16px;height:89px;background:var(--gold)}
.accent-corner-bottom{left:584px;top:425px;width:146px;height:9px;background:var(--gold)}
.accent-steel{left:683px;top:303px;width:31px;height:6px;background:var(--steel-light)}

/* stripes */
.stripe{height:8px;display:flex}
.stripe span{height:100%}

/* welcome */
.welcome-title{left:145px;top:516px;font-size:38px;font-weight:700;color:var(--gold)}
.welcome-body{left:145px;top:586px;width:490px;font-size:12.3px;line-height:24.3px}
.welcome-body p{margin-bottom:24.3px}
.more-link{left:523px;top:952px;font-size:14.5px;font-weight:700;color:var(--gold);text-decoration:none;border-bottom:2px dotted var(--gold);padding-bottom:2px}

/* sidebar */
.side-title{font-size:23px;font-weight:700;color:var(--gold)}
.contact-list{left:689px;top:569px;width:219px;border-top:1px solid #4a4f57}
.contact-row{display:flex;border-bottom:1px solid #4a4f57}
.contact-row:last-child{border-bottom:none}
.contact-icon{width:29px;border-right:1px solid #4a4f57;display:flex;justify-content:center;padding-top:10px}
.contact-text{padding:9px 0 9px 13px;font-size:12.2px;line-height:16px}
.contact-text.phone{font-size:19px;font-weight:600;line-height:24px;padding:8px 0 9px 13px}
.social{display:flex;gap:15px}
.social span{width:26px;height:26px;border-radius:50%}
.follow-rule{left:689px;top:868px;width:219px;height:1px;background:#4a4f57}

/* footer */
.footer{left:0;top:1054px;width:1054px;height:146px;background:var(--footer)}
.brands-label{left:147px;top:1077px;color:var(--text-dark);line-height:1}
.brands-label b{display:block;font-size:19px;font-weight:400;letter-spacing:.5px}
.brands-label small{display:block;font-size:14px;font-weight:600;margin-top:4px}
.partner{top:1083px;height:28px;display:flex;align-items:center;gap:6px;font-size:22px;font-weight:700}
.partner .sq{width:22px;height:22px}
.copyright{left:147px;top:1163px;font-size:11px;color:var(--text-dark)}
</style>
</head>
<body>
<div class="page">

  <header class="header abs">
    <div class="header-phone abs">
      <svg width="18" height="18" viewBox="0 0 24 24" aria-hidden="true"><path fill="#e5b54a" d="M6.6 10.8c1.4 2.8 3.8 5.1 6.6 6.6l2.2-2.2c.3-.3.7-.4 1-.2 1.1.4 2.3.6 3.6.6.6 0 1 .4 1 1V20c0 .6-.4 1-1 1C10.6 21 3 13.4 3 4c0-.6.4-1 1-1h3.5c.6 0 1 .4 1 1 0 1.3.2 2.5.6 3.6.1.3 0 .7-.2 1z"/></svg>
      1300 47 19 62
    </div>
    <nav class="main-nav abs">
      <a class="active" href="#">HOME</a><a href="#">ABOUT US</a><a href="#">SERVICES</a><a href="#">TESTIMONIALS</a><a href="#">SHOWCASE</a><a href="#">CONTACT US</a>
    </nav>
  </header>

  <div class="hero abs" role="img" aria-label="Photograph of a painted living room with a cream and brown leather sofa"></div>

  <div class="brand-mark abs" aria-hidden="true"></div>
  <div class="brand-ribbon abs">
    <span class="brand-name">KELBRIDGE PAINTING</span>
    <span class="brand-divider"></span>
    <span class="brand-tagline">Painting Australia Everyday!</span>
  </div>

  <div class="slider-dots abs"><span></span><span></span><span></span><span class="on"></span></div>

  <div class="accent-top-left abs"></div>
  <div class="accent-left abs"></div>
  <div class="accent-corner-right abs"></div>
  <div class="accent-corner-bottom abs"></div>
  <div class="hero-caption abs">We paint residential,<br>commercial and strata jobs</div>
  <div class="accent-steel abs"></div>

  <div class="stripe abs" style="left:0;top:478px;width:1054px">
    <span style="width:252px;background:var(--ink)"></span>
    <span style="width:72px;background:#4f545b"></span>
    <span style="width:80px;background:#6d7177"></span>
    <span style="width:124px;background:#9a9da2"></span>
    <span style="width:106px;background:var(--gold-deep)"></span>
    <span style="width:72px;background:#e0ac3a"></span>
    <span style="width:80px;background:#eec06a"></span>
    <span style="width:268px;background:var(--gold-pale)"></span>
  </div>

  <main>
    <h1 class="welcome-title abs">Welcome!</h1>
    <div class="welcome-body abs">
      <p>Lorem ipsum dolor sit amet, consectetur adipiscing elit. Quantum Aristoxeni ingenium consumptum videmus in musicis? Nihil enim hoc differt. Re mihi non aeque satisfacit, et quidem locis pluribus. At iste non dolendi status non vocatur voluptas. Quamquam haec quidem praeposita recte et reiecta dicere licebit.</p>
      <p>Duo Reges: constructio interrete. Inde sermone vario sex illa a Dipylo stadia confecimus. Ad quorum et cognitionem et usum iam corroborati natura ipsa praeeunte deducimur. Idem iste, inquam, de voluptate quid sentit? Septem autem illi non suo, sed populorum suffragio omnium nominati sunt. Quamquam haec quidem praeposita recte et reiecta dicere licebit. Atqui eorum nihil est eius generis, ut sit in fine atque extremo bonorum.</p>
      <p>Atqui reperies, inquit, in hoc quidem pertinacem; Sin autem est in ea, quod quidam volunt, nihil impedit hanc nostram comprehensionem summi boni. Urgent tamen et nihil remittunt. Avaritiamne minuis.</p>
    </div>
    <a class="more-link abs" href="#">MORE ABOUT US</a>
  </main>

  <aside>
    <h2 class="side-title abs" style="left:689px;top:530px">Contact us</h2>
    <div class="contact-list abs">
      <div class="contact-row">
        <div class="contact-icon"><svg width="18" height="20" viewBox="0 0 18 20" aria-hidden="true"><path fill="#8d9096" d="M8 1h2v18H8zM3 4h12l2 2-2 2H3zM2 9h6v3H2L0 10.5z"/></svg></div>
        <div class="contact-text">Lorem ipsum dolor sit amet consectetur adipiscing elit Quantum Aristoxeni ingenium consumptum.</div>
      </div>
      <div class="contact-row">
        <div class="contact-icon"><svg width="16" height="16" viewBox="0 0 24 24" aria-hidden="true"><path fill="#8d9096" d="M6.6 10.8c1.4 2.8 3.8 5.1 6.6 6.6l2.2-2.2c.3-.3.7-.4 1-.2 1.1.4 2.3.6 3.6.6.6 0 1 .4 1 1V20c0 .6-.4 1-1 1C10.6 21 3 13.4 3 4c0-.6.4-1 1-1h3.5c.6 0 1 .4 1 1 0 1.3.2 2.5.6 3.6.1.3 0 .7-.2 1z"/></svg></div>
        <div class="contact-text phone">1300 47 19 62</div>
      </div>
      <div class="contact-row">
        <div class="contact-icon"><svg width="18" height="13" viewBox="0 0 18 13" aria-hidden="true"><rect x="0.5" y="0.5" width="17" height="12" fill="none" stroke="#8d9096"/><path d="M1 1l8 6 8-6M1 12l6-5M17 12l-6-5" fill="none" stroke="#8d9096"/></svg></div>
        <div class="contact-text">mail@kelbridgepainting.com.au</div>
      </div>
    </div>

    <h2 class="side-title abs" style="left:689px;top:773px">Follow us</h2>
    <div class="social abs" style="left:690px;top:826px" aria-label="Social links">
      <span style="background:#3f62a8"></span><span style="background:#c4c6c9"></span><span style="background:#c4c6c9"></span><span style="background:#c4c6c9"></span>
    </div>
    <div class="follow-rule abs"></div>
  </aside>

  <div class="stripe abs" style="left:0;top:1046px;width:1054px">
    <span style="width:268px;background:var(--gold-pale)"></span>
    <span style="width:80px;background:#eec06a"></span>
    <span style="width:72px;background:#e0ac3a"></span>
    <span style="width:106px;background:var(--gold-deep)"></span>
    <span style="width:124px;background:#9a9da2"></span>
    <span style="width:80px;background:#6d7177"></span>
    <span style="width:72px;background:#4f545b"></span>
    <span style="width:252px;background:var(--ink)"></span>
  </div>

  <footer class="footer abs"></footer>
  <div class="brands-label abs"><b>BRANDS</b><small>USED BY US</small></div>
  <div class="partner abs" style="left:278px;color:#1f2b5c">Covella</div>
  <div class="partner abs" style="left:417px;color:#1f2b5c">Brennick</div>
  <div class="partner abs" style="left:553px;color:#23262b"><span class="sq" style="background:#e0533a"></span>Marlowe</div>
  <div class="partner abs" style="left:752px;color:#4a4d52">Duraveil</div>

  <p class="copyright abs">Copyright @ 2013 Kelbridge Painting. All rights reserved.</p>
  <div class="social abs" style="left:759px;top:1159px" aria-label="Social links">
    <span style="background:#3f62a8"></span><span style="background:#2a2d33"></span><span style="background:#2a2d33"></span><span style="background:#2a2d33"></span>
  </div>

</div>
</body>
</html>
```